New name flyer

We have just changed our business name from Wattlebay Realty to Harbor Lantern. We want to distribute a flyer to the local community to inform them of the change. We are a realestate agency which focuses mainly on property management but also sales. We service from Brisbane to the Sunshine coast.

Target Market(s)

Local community

Industry/Entity Type

realestate

Requirements
Must have
• Details of name change
Nice to have
• Servicing area Brisbane and Sunshine Coast, no change in management or services we offer, and will continue pride ourselves on offering a high level of service, with the same team from the Gold to Sunshine Coast.
Should not have
• too much wording.

```html
<!DOCTYPE html>
<html lang="en">
<head>
<meta charset="utf-8">
<title>Harbor Lantern – New Name Flyer</title>
<link rel="stylesheet" href="https://fonts.googleapis.com/css2?family=Barlow+Condensed:wght@500;700&family=Questrial&family=Montserrat:wght@600;700&display=swap">
<style>
  :root {
    --navy: #1d3260;
    --gold: #c9962f;
    --white: #ffffff;
    --backdrop: #7a7a7a;
    --photo-dark: #3b3d48;
    --photo-warm: #a88e72;
    --photo-pool: #4fa6c4;
  }
  * { margin: 0; padding: 0; box-sizing: border-box; }
  html, body { width: 1200px; height: 920px; overflow: hidden; background: var(--backdrop); }
  .flyer {
    position: absolute; left: 94px; top: 79px;
    width: 1052px; height: 744px;
    background: var(--navy); overflow: hidden;
  }
  .header { position: absolute; left: 0; top: 0; width: 1052px; height: 239px; }
  .header svg { position: absolute; left: 0; top: 0; }
  .old-name {
    position: absolute; left: 20px; top: 104px; width: 260px;
    font-family: "Questrial", sans-serif; font-size: 26px; line-height: 1.1;
    color: var(--navy); text-align: center;
  }
  .headline {
    position: absolute; left: 366px; top: 70px; width: 280px;
    text-align: center; font-family: "Barlow Condensed", sans-serif; line-height: 0.9;
  }
  .headline .line-one { display: block; font-size: 70px; font-weight: 500; color: var(--white); }
  .headline .line-two { display: block; font-size: 70px; font-weight: 700; color: var(--gold); }
  .new-name {
    position: absolute; left: 743px; top: 98px; width: 290px;
    font-family: "Montserrat", sans-serif; font-weight: 700; font-size: 34px;
    line-height: 1.1; color: var(--white); letter-spacing: 2px;
  }
  .photo {
    position: absolute; left: 0; top: 239px; width: 1052px; height: 434px;
    background: linear-gradient(180deg, var(--photo-dark) 0%, var(--photo-warm) 55%, var(--photo-dark) 85%, var(--photo-pool) 100%);
  }
  .message {
    position: absolute; left: 89px; top: 505px; width: 900px; height: 144px;
    background: var(--navy); color: var(--white); text-align: center;
    padding-top: 12px;
  }
  .message .area { font-family: "Questrial", sans-serif; font-size: 26px; line-height: 30px; }
  .message .promise {
    font-family: "Montserrat", sans-serif; font-weight: 700; font-size: 24.5px;
    line-height: 31px; color: var(--gold);
  }
  .message .details { font-family: "Questrial", sans-serif; font-size: 26px; line-height: 29px; }
  .contact-bar {
    position: absolute; left: 0; top: 673px; width: 1052px; height: 71px;
    background: var(--gold); display: flex; align-items: center; justify-content: center;
    gap: 10px; color: var(--white); font-size: 24px;
  }
  .contact-bar .icon { width: 24px; height: 24px; flex: none; }
  .contact-bar .phone { font-family: "Montserrat", sans-serif; font-weight: 600; margin-right: 10px; }
  .contact-bar .web { font-family: "Questrial", sans-serif; font-size: 22px; letter-spacing: 0.5px; }
  .contact-bar .web strong { font-family: "Montserrat", sans-serif; font-weight: 600; }
</style>
</head>
<body>
  <main class="flyer">
    <header class="header">
      <svg width="1052" height="239" viewBox="0 0 1052 239" aria-hidden="true">
        <polygon class="white-panel" points="0,0 252,0 332,120 252,239 0,239" fill="#ffffff"/>
        <polyline points="256,0 336,120 256,239" fill="none" stroke="#c9962f" stroke-width="6"/>
        <polyline points="270,0 350,120 270,239" fill="none" stroke="#c9962f" stroke-width="4"/>
        <polyline points="618,0 698,120 618,239" fill="none" stroke="#c9962f" stroke-width="6"/>
        <polyline points="632,0 712,120 632,239" fill="none" stroke="#c9962f" stroke-width="4"/>
      </svg>
      <div class="old-name">Wattlebay Realty</div>
      <h1 class="headline">
        <span class="line-one">WE HAVE</span>
        <span class="line-two">CHANGED</span>
      </h1>
      <div class="new-name">HARBOR<br>LANTERN</div>
    </header>

    <div class="photo" role="img" aria-label="Photograph of a modern two-storey home with lit windows and a pool at dusk"></div>

    <section class="message">
      <p class="area">Servicing area Brisbane &amp; Sunshine Coast</p>
      <p class="promise">NO CHANGE IN MANAGEMENT OR SERVICES</p>
      <p class="details">we offer &amp; will continue pride ourselves on offering a high level of service<br>with the same team from the Gold to Sunshine Coast.</p>
    </section>

    <footer class="contact-bar">
      <svg class="icon" viewBox="0 0 24 24" aria-hidden="true">
        <circle cx="12" cy="12" r="12" fill="#ffffff"/>
        <path d="M8.2 6.5l2 2.3-1.2 1.5c.8 1.7 2 2.9 3.7 3.7l1.5-1.2 2.3 2-1.2 1.8c-4.2-.4-8.2-4.4-8.6-8.6z" fill="#c9962f"/>
      </svg>
      <span class="phone">555-014-2368</span>
      <svg class="icon" viewBox="0 0 24 24" aria-hidden="true">
        <circle cx="12" cy="12" r="12" fill="#ffffff"/>
        <g fill="none" stroke="#c9962f" stroke-width="1.3">
          <circle cx="12" cy="12" r="6.5"/>
          <ellipse cx="12" cy="12" rx="3" ry="6.5"/>
          <line x1="5.5" y1="12" x2="18.5" y2="12"/>
          <line x1="6.5" y1="8.8" x2="17.5" y2="8.8"/>
          <line x1="6.5" y1="15.2" x2="17.5" y2="15.2"/>
        </g>
      </svg>
      <span class="web">WWW.<strong>HARBORLANTERN</strong>.COM</span>
    </footer>
  </main>
</body>
</html>
```